Redesign of business card for Cedar Ridge Mechanical

We are looking for a new design for our business cards for Cedar Ridge Mechanical. We are a plumbing & HVAC construction company, operating on the West Coast of Canada and USA. Logo attached.
Industry/Entity Type
Construction - Plumbing & HVAC
Contact Information for Business Card
Name, address, phone numbers, email, website address
Look and feel
Each slider illustrates characteristics of the customer's brand and the style your logo design should communicate.

```html
<!DOCTYPE html>
<html lang="en">
<head>
<meta charset="utf-8">
<title>Cedar Ridge Mechanical – Business Card</title>
<link rel="stylesheet" href="https://fonts.googleapis.com/css2?family=Arimo:wght@400&family=Roboto+Condensed:wght@700&display=swap">
<style>
  :root {
    --page-bg: #d8d3cb;
    --card-bg: #ecebe8;
    --card-edge: #b9b6b1;
    --ink: #1c1c1c;
    --ink-soft: #2a2a2a;
    --bar: #121212;
    --web-gold: #b8966d;
  }
  * { margin: 0; padding: 0; box-sizing: border-box; }
  html, body {
    width: 1170px;
    height: 1200px;
    overflow: hidden;
    background: var(--page-bg);
  }
  .card {
    position: absolute;
    left: 60px;
    top: 301px;
    width: 1050px;
    height: 598px;
    background: var(--card-bg);
    border: 1.5px solid var(--card-edge);
    border-radius: 30px;
    overflow: hidden;
    font-family: "Arimo", Arial, sans-serif;
    color: var(--ink);
  }
  .brand {
    position: absolute;
    left: 62px;
    top: 150px;
    display: flex;
    align-items: center;
    gap: 16px;
    font-family: "Roboto Condensed", "Arial Narrow", sans-serif;
    font-weight: 700;
    font-size: 30px;
    letter-spacing: 0.5px;
    color: var(--ink);
    text-transform: uppercase;
  }
  .brand-mark {
    width: 30px;
    height: 30px;
    background: var(--ink);
  }
  .person {
    position: absolute;
    right: 46px;
    top: 76px;
    text-align: right;
  }
  .person-name {
    font-family: "Roboto Condensed", "Arial Narrow", sans-serif;
    font-weight: 700;
    font-size: 40px;
    line-height: 1.1;
    color: var(--ink);
  }
  .person-title {
    font-size: 24px;
    line-height: 1.3;
    color: var(--ink-soft);
  }
  .address {
    position: absolute;
    right: 46px;
    top: 258px;
    text-align: right;
    font-size: 24px;
    line-height: 33px;
  }
  .contacts {
    position: absolute;
    right: 46px;
    top: 366px;
    list-style: none;
    text-align: right;
    font-size: 24px;
    line-height: 33px;
  }
  .contacts li {
    display: flex;
    justify-content: flex-end;
    align-items: center;
    gap: 8px;
  }
  .contacts svg { width: 22px; height: 22px; fill: var(--ink); }
  .web-bar {
    position: absolute;
    left: 522px;
    right: 0;
    top: 479px;
    height: 56px;
    background: var(--bar);
    border-radius: 10px 0 0 10px;
    display: flex;
    align-items: center;
    justify-content: flex-end;
    padding-right: 46px;
    font-size: 24px;
    color: var(--web-gold);
  }
</style>
</head>
<body>
  <article class="card">
    <div class="brand">
      <span class="brand-mark"></span>
      <span class="brand-name">Cedar Ridge Mechanical</span>
    </div>

    <header class="person">
      <p class="person-name">Martin Hale</p>
      <p class="person-title">President</p>
    </header>

    <address class="address" style="font-style:normal">
      2217 Harbour View Road<br>
      Lakeside, WA 98012
    </address>

    <ul class="contacts">
      <li>(604) 5218-3390
        <svg viewBox="0 0 24 24" aria-hidden="true"><path d="M6.6 10.8a15.1 15.1 0 0 0 6.6 6.6l2.2-2.2c.3-.3.7-.4 1-.2 1.1.4 2.3.6 3.6.6.6 0 1 .4 1 1V20c0 .6-.4 1-1 1A17 17 0 0 1 3 4c0-.6.4-1 1-1h3.5c.6 0 1 .4 1 1 0 1.3.2 2.5.6 3.6.1.3 0 .7-.2 1z"/></svg>
      </li>
      <li>name@cedarridgemechanical.com
        <svg viewBox="0 0 24 24" aria-hidden="true"><path d="M2 6h20v12H2z" /><path d="M2 6l10 7 10-7" fill="none" stroke="#ecebe8" stroke-width="1.6"/></svg>
      </li>
    </ul>

    <div class="web-bar">www.cedarridgemechanical.com</div>
  </article>
</body>
</html>
```